Aquatic View

We need a web design for a new window cleaning company name Tidewell Glass Care. We are located in Grand Cayman, Cayman Islands. We are a small company, a team of husband and wife. Our services include residencial interior and exterior window cleaning and commercial. Extra services such as ceiling fans cleaning, mirrors, high dusting. Home cleaning services. Power washing. Explaining the service. We want a modern, beachy style with aquatic colors. We want to use our domain name "tidewellglasscare.ky". We want to portray a clean, modern and professional design.

Target Market(s)

Big Home owners

Industry/Entity Type

Cleaning Service

Contact Information for Business Card

Company Name: Tidewell Glass Care
Name: Desmond Farrowby owner/manager
Phone: 345-9170452
Email: desmond@tidewellglasscare.ky
Website: tidewellglasscare.ky
Address: P.O.Box 2486 GT, George Town, Grand Cayman KY1-1203 Cayman Islands

Number of Pages Required

2 page

Font styles to use
Sans Serif

Colors
0592cd
0455a3
33a6d7
85cae6
cadf82
abd036
fbf289

Requirements
Nice to have
• Pictures of an ocean view and palm trees from clear windows.
• https://quorvantel.com/bidlinker/
• Use the above for "free estimate".

```html
<!DOCTYPE html>
<html lang="en">
<head>
<meta charset="utf-8">
<title>Tidewell Glass Care</title>
<link rel="stylesheet" href="https://fonts.googleapis.com/css2?family=Lato:wght@400;700&family=Open+Sans:wght@600;700&family=Outfit:wght@500;600&display=swap">
<style>
:root{
  --ocean:#0592cd;
  --deep:#0455a3;
  --sky:#33a6d7;
  --mist:#85cae6;
  --ink:#2b2b2b;
  --text:#3a3a3a;
  --rule:#d6d6d6;
  --footer:#ececec;
}
*{box-sizing:border-box;margin:0;padding:0}
html,body{width:966px;height:1200px;overflow:hidden;background:#fff}
body{position:relative;font-family:'Lato',sans-serif;color:var(--text)}
.topbar{position:absolute;left:0;top:0;width:966px;height:32px;background:linear-gradient(180deg,var(--deep),var(--ocean))}
.header{position:absolute;left:0;top:32px;width:966px;height:48px;background:#fff}
.brand{position:absolute;left:90px;top:42px;display:flex;align-items:center;gap:8px;font-family:'Outfit',sans-serif;font-weight:600;font-size:19px;color:var(--deep)}
.brand-dot{width:22px;height:22px;border-radius:50%;background:var(--ocean)}
.nav{position:absolute;top:43px;left:574px;display:flex;font-family:'Open Sans',sans-serif;font-weight:700;font-size:12.5px}
.nav a{color:var(--deep);text-decoration:none;height:28px;line-height:28px;padding:0 9px;margin-right:15px}
.nav a.active{background:var(--ocean);color:#fff}
.hero{position:absolute;left:0;top:80px;width:966px;height:424px;
  background:linear-gradient(22deg,#1f242c 0%,#2f3744 18%,#5d7693 32%,#8fb6da 46%,#c4dcf1 62%,#e6eff8 78%,#a7c8e8 100%)}
.hero-arrow{position:absolute;top:166px;width:32px;height:32px;border-radius:50%;background:#f4f4f4;border:2px solid #bdbdbd}
.hero-arrow svg{position:absolute;left:8px;top:8px}
.hero-caption{position:absolute;left:0;bottom:0;width:966px;height:46px;background:rgba(60,60,60,.72);color:#fff;font-family:'Open Sans',sans-serif;font-weight:700;font-size:23.5px;text-align:center;line-height:48px}
.welcome{position:absolute;left:80px;top:540px;width:511px}
.welcome h1{font-family:'Outfit',sans-serif;font-weight:600;font-size:26px;color:var(--ink);line-height:30px}
.welcome h1 span{color:var(--deep)}
.welcome hr{border:0;border-top:1px solid var(--rule);margin:12px 0 12px}
.welcome h2{font-size:14px;font-weight:700;color:var(--ink)}
.welcome h2 span{color:var(--deep);font-weight:400}
.welcome p{font-size:12.3px;line-height:19.5px;margin-top:15px;color:#444}
.btn{display:inline-block;background:var(--ocean);color:#fff;font-weight:700;font-size:11.5px;text-decoration:none}
.read-more{position:absolute;left:80px;top:738px;width:83px;height:27px;line-height:27px;text-align:center}
.inquiry{position:absolute;left:611px;top:555px;width:276px;height:218px;border:1px solid var(--rule)}
.inquiry-tab{position:absolute;left:58px;top:-11px;width:181px;height:34px;background:var(--ocean);color:#fff;font-family:'Open Sans',sans-serif;font-weight:700;font-size:14.5px;text-align:center;line-height:34px;letter-spacing:.5px}
.inquiry-tab::before,.inquiry-tab::after{content:"";position:absolute;top:0;border-bottom:11px solid var(--deep)}
.inquiry-tab::before{left:-8px;border-left:8px solid transparent}
.inquiry-tab::after{right:-8px;border-right:8px solid transparent}
.field{position:absolute;left:19px;width:243px;height:27px;border:1px solid #c8c8c8;border-radius:2px;background:linear-gradient(#f7f7f7,#e9e9e9);font-size:11px;color:#222;padding:6px 6px}
.field i{color:#d9302c;font-style:normal}
.submit{position:absolute;left:20px;top:182px;width:89px;height:27px;line-height:27px;text-align:center;font-weight:400;font-size:12.5px}
.services{position:absolute;left:0;top:812px;width:966px;text-align:center}
.services h2{font-family:'Outfit',sans-serif;font-weight:600;font-size:26px;color:var(--ink)}
.services h2 span{color:var(--deep)}
.services .rule{position:relative;width:587px;height:1px;background:var(--rule);margin:17px auto 0}
.services .rule svg{position:absolute;left:284px;top:-7px}
.services p{font-size:14.5px;color:#333;margin-top:13px}
.card{position:absolute;top:919px;width:245px;height:169px}
.card .photo{height:134px}
.card h3{height:35px;line-height:36px;background:var(--ocean);color:#fff;font-family:'Outfit',sans-serif;font-weight:600;font-size:16.5px;padding-left:10px}
.photo-home{background:linear-gradient(120deg,#4d7d3e 0%,#c9d6de 22%,#eef1f3 45%,#c7b79c 65%,#8a5a35 85%,#2f3e6e 100%)}
.photo-office{background:linear-gradient(160deg,#8c6b4a 0%,#c29a6c 25%,#e8e2d8 55%,#f0c33a 75%,#d8cfc2 100%)}
.photo-extra{background:linear-gradient(100deg,#3f4043 0%,#7a7c80 18%,#d9dcdf 40%,#f3f4f5 70%,#c9ccd0 100%)}
.footer-line{position:absolute;left:0;top:1128px;width:966px;height:2px;background:var(--ocean)}
.footer{position:absolute;left:0;top:1130px;width:966px;height:70px;background:var(--footer)}
.footer-nav{position:absolute;left:77px;top:26px;font-size:11.5px;color:#333}
.footer-nav span{margin:0 9px}
.footer-brand{position:absolute;left:410px;top:24px;width:146px;text-align:center;font-family:'Outfit',sans-serif;font-weight:600;font-size:14px;color:#555}
.copyright{position:absolute;right:85px;top:27px;font-size:11px;color:#333}
</style>
</head>
<body>
<div class="topbar"></div>
<header class="header"></header>
<div class="brand"><span class="brand-dot"></span>Tidewell Glass Care</div>
<nav class="nav">
  <a class="active" href="#">HOME</a><a href="#">ABOUT</a><a href="#">SERVICES</a><a href="#">CONTACT</a>
</nav>

<section class="hero" role="img" aria-label="Window cleaner wiping a tall glass pane with a squeegee against a blue, cloudy sky">
  <div class="hero-arrow" style="left:25px"><svg width="12" height="12" viewBox="0 0 12 12"><path d="M8 1 3 6l5 5" fill="none" stroke="#222" stroke-width="2.4"/></svg></div>
  <div class="hero-arrow" style="left:907px"><svg width="12" height="12" viewBox="0 0 12 12"><path d="M4 1l5 5-5 5" fill="none" stroke="#222" stroke-width="2.4"/></svg></div>
  <div class="hero-caption">WE ARE RESIDENTIAL, COMMERCIAL CLEANING SERVICE FIRM</div>
</section>

<section class="welcome">
  <h1>Welcome To <span>Tidewell Glass Care</span></h1>
  <hr>
  <h2><span>Tidewell Glass Care</span> dolor sit amet, consectetuer adipiscing elit, sed dia</h2>
  <p>Lorem ipsum dolor sit amet, consectetuer adipiscing elit, sed diam nonummy nibh euismod tincidunt ut laoreet dolore magna aliquam erat volutpat. Ut wisi enim ad minim veniam, quis nostrud exerci tation ullamcorper suscipit lobortis nisl ut aliquip ex ea commodo consequat. Duis autem vel eum iriure dolor in hendrerit in vulputate velit.</p>
</section>
<a class="btn read-more" href="#">READ MORE</a>

<form class="inquiry">
  <div class="inquiry-tab">QUICK INQUIRY</div>
  <div class="field" style="top:31px">First Name <i>*</i></div>
  <div class="field" style="top:65px">Last Name <i>*</i></div>
  <div class="field" style="top:98px">Email <i>*</i></div>
  <div class="field" style="top:131px;height:45px">Address<i>*</i></div>
  <a class="btn submit" href="#">SUBMIT</a>
</form>

<section class="services">
  <h2>Our <span>Services</span></h2>
  <div class="rule"><svg width="20" height="8" viewBox="0 0 20 8"><path d="M1 8A9 7 0 0 1 19 8Z" fill="#fff" stroke="#777" stroke-width="1"/></svg></div>
  <p>Lorem ipsum dolor sit amet, consectetuer adipiscing elit, sed diam nonummy nibh euismod tincidunt ut</p>
</section>

<div class="card" style="left:79px">
  <div class="photo photo-home" role="img" aria-label="Cleaners in blue overalls washing kitchen windows in a home"></div>
  <h3>Residential</h3>
</div>
<div class="card" style="left:360px">
  <div class="photo photo-office" role="img" aria-label="Staff mopping a tiled office lobby floor beside yellow wet-floor signs"></div>
  <h3>Commercial</h3>
</div>
<div class="card" style="left:642px">
  <div class="photo photo-extra" role="img" aria-label="Worker cleaning tall interior glass panels of a modern building"></div>
  <h3>Extra Services</h3>
</div>

<div class="footer-line"></div>
<footer class="footer">
  <div class="footer-nav">HOME<span>|</span>ABOUT<span>|</span>SERVICES<span>|</span>CONTACT</div>
  <div class="footer-brand">Tidewell Glass Care</div>
  <div class="copyright">© 2015 Tidewell Glass Care. All Rights Reserved</div>
</footer>
</body>
</html>
```